Website Design Required For Education Video Portfolio Site

I am looking for a designer to create a skin for a relaunch of my website - www.brackenlearningfilms.co.uk. We want a clean and stylish new design.

The website showcases prospectus/promotional videos that are made for schools and colleges. Videos will be hosted on YouTube and embedded.

I want it to be stylish and clean.

I require 7 pages designed and this must be agreed in order to do the project.

1. Homepage
2. About
3. Prices
4. Testimonials
5. Contact Page with form
6. Promotional Videos
7. Subject Videos

The website will be then be built on the Wordpress system.

Target Market(s)

Education, Schools, Colleges, Universities

Industry/Entity Type

Education

Font styles to use
Serif

Colors

Designer to choose colors to be used in the design.

Requirements
Must have
• Video content, be clean, show our portfolio, descriptions about videos. I like the idea of having video headers.
Nice to have
• Images

```html
<!DOCTYPE html>
<html lang="en">
<head>
<meta charset="utf-8">
<title>Bracken Learning Films</title>
<link href="https://fonts.googleapis.com/css2?family=Kanit:wght@300;400;500;600&display=swap" rel="stylesheet">
<style>
:root{
  --blue:#1ab2e8;
  --blue-dark:#0f8fc4;
  --band:#cdeefb;
  --ink:#1d1d1f;
  --muted:#3a3a3a;
  --line:#d9d9d9;
  --black:#000;
  --white:#fff;
}
*{margin:0;padding:0;box-sizing:border-box}
html,body{width:1200px;height:4317px;overflow:hidden;background:var(--white)}
body{position:relative;font-family:'Kanit',sans-serif;color:var(--ink)}
.abs{position:absolute}

/* header */
.brand{left:110px;top:38px;display:flex;align-items:center;gap:10px;color:var(--blue);font-weight:600;font-size:22px;line-height:1;white-space:nowrap}
.brand-square{width:30px;height:30px;background:var(--blue);border-radius:6px}
.nav{left:425px;top:45px;display:flex;gap:44px;font-size:14.5px;font-weight:500}
.nav span{display:flex;align-items:center;gap:6px}
.search{left:1058px;top:40px;width:28px;height:28px;background:var(--blue);border-radius:5px;display:flex;align-items:center;justify-content:center}

/* hero */
.hero{left:0;top:100px;width:1200px;height:513px;border-radius:0 70px 70px 0;overflow:hidden;
  background:linear-gradient(90deg,#cfae8c 0%,#9c7a5d 30%,#5a4a40 55%,#1e1d20 75%,#0e0e10 100%)}
.hero-text{left:731px;top:205px;width:440px;color:var(--white)}
.hero-brand{display:flex;align-items:center;gap:12px;font-size:32px;font-weight:600;line-height:1;white-space:nowrap}
.hero-brand i{width:40px;height:40px;background:var(--white);border-radius:8px;display:block;flex:none}
.hero-text h1{font-size:33px;font-weight:500;margin-top:48px;line-height:1}
.hero-text p{font-size:18.5px;font-weight:500;margin-top:26px;line-height:1}
.hero-text p + p{margin-top:30px}

/* section heading */
.heading{display:flex;align-items:center;gap:12px;font-size:31px;font-weight:500;line-height:1;transform:translateX(-50%)}
.heading .sq{width:28px;height:28px;background:var(--ink);border-radius:5px}
.heading b{color:var(--blue);font-weight:500}

/* about */
.about-copy{left:110px;top:852px;width:482px;font-size:14.8px;font-weight:300;line-height:32.7px;text-align:justify}
.about-copy p+p{margin-top:11px}
.about-frame{left:666px;top:818px;width:372px;height:398px;border:3px solid var(--blue);border-radius:18px}
.about-photo{left:654px;top:808px;width:374px;height:398px;border-radius:16px;
  background:linear-gradient(160deg,#3d8f86 0%,#7ab3a8 35%,#d9b58e 65%,#8c6a4e 100%)}

/* prices */
.prices-band{left:0;top:1307px;width:1200px;height:600px;background:var(--band);border-radius:45px}
.price-card{top:1450px;width:259px;height:357px;background:var(--white)}
.price-head{height:67px;background:var(--blue);border-radius:0 45px 0 0;color:var(--white);
  font-size:14px;font-weight:500;text-align:center;display:flex;flex-direction:column;justify-content:center;line-height:30px}
.price-from{color:var(--blue);font-size:19px;font-weight:500;text-align:center;margin-top:28px}
.price-list{list-style:none;margin:14px 0 0 22px;font-size:14.8px;font-weight:300;line-height:37px;width:220px}
.price-list li{position:relative;padding-left:21px}
.price-list li::before{content:"";position:absolute;left:0;top:14px;border-left:8px solid var(--ink);border-top:4.5px solid transparent;border-bottom:4.5px solid transparent}
.price-btn{position:absolute;left:50px;top:301px;width:163px;height:40px;background:var(--blue);color:var(--white);
  border-radius:22px 22px 0 22px;font-size:15.5px;font-weight:500;display:flex;align-items:center;justify-content:center}
.dots{display:flex;gap:10px}
.dots i{display:block;width:32px;height:5px;border-radius:3px;background:#8a8a8a}
.dots i.on{background:var(--blue)}

/* promo videos */
.video-card{top:2080px;width:317px;height:367px;border:2px solid #e6e6e6;border-radius:12px;overflow:hidden;background:var(--white);text-align:center}
.thumb{height:228px;display:flex;align-items:center;justify-content:center}
.play{width:30px;height:30px;background:var(--white);border-radius:4px;display:flex;align-items:center;justify-content:center}
.video-card h3{color:var(--blue);font-size:21px;font-weight:500;margin-top:34px}
.video-card p{font-size:17px;font-weight:300;margin-top:20px}

/* subject videos */
.tab{top:2668px;width:367px;height:64px;border-radius:10px;font-size:23px;font-weight:500;display:flex;align-items:center;justify-content:center}
.tab-outline{left:223px;border:2px solid var(--blue);background:var(--white)}
.tab-solid{left:610px;background:var(--blue);color:var(--white)}
.subject-intro{left:0;top:2773px;width:1200px;text-align:center;font-size:15px;font-weight:300;line-height:39px}
.tiles{left:104px;top:2891px;width:990px;height:221px;display:flex;gap:3px;border-radius:14px;overflow:hidden}
.tile{flex:1;background:linear-gradient(180deg,#35bff0,#1aa6de);color:var(--white);display:flex;flex-direction:column;align-items:center;justify-content:flex-end;padding-bottom:22px;text-align:center}
.tile-icon{width:86px;height:80px;border:2px solid rgba(255,255,255,.55);border-radius:10px;margin-bottom:16px}
.tile h4{font-size:20px;font-weight:500;line-height:28px}
.tile .go{width:30px;height:30px;border-radius:50%;background:var(--white);margin-top:12px;display:flex;align-items:center;justify-content:center}

/* testimonials */
.heading-left{left:110px;top:3218px;transform:none}
.avatar{top:3212px;width:80px;height:80px;border-radius:50%;border:3px solid #e8e8e8}
.testi-box{left:129px;top:3334px;width:944px;height:390px;border:2px solid #d4d4d4;border-radius:12px}
.testi-photo{left:142px;top:3350px;width:354px;height:357px;border-radius:14px;background:linear-gradient(160deg,#4d8fcf,#2f74b8 60%,#25609c)}
.quote{left:536px;top:3366px;width:481px;font-size:14.8px;font-weight:300;line-height:32.7px;text-align:justify}
.testi-name{left:536px;top:3574px;color:var(--blue);font-size:20px;font-weight:500}
.testi-role{left:536px;top:3618px;font-size:13px;font-weight:500}
.stars{left:536px;top:3662px;display:flex;gap:6px}
.arrow-btn{top:3676px;width:33px;height:33px;background:var(--blue);border-radius:6px;display:flex;align-items:center;justify-content:center}

/* footer */
.footer{left:0;top:3821px;width:1200px;height:496px;background:var(--black);border-radius:60px 60px 0 0;color:var(--white)}
.foot-title{color:var(--blue);font-size:21px;font-weight:500}
.foot-links{list-style:none;font-size:15.5px;font-weight:300;line-height:41px}
.contact-row{display:flex;align-items:center;gap:20px;font-size:15.5px;font-weight:300}
.contact-icon{width:40px;height:40px;border:2px solid var(--white);border-radius:8px;display:flex;align-items:center;justify-content:center;flex:none}
.field{left:786px;width:302px;height:54px;background:#1e1e1e;border-radius:6px;font-size:13px;font-weight:500;padding-left:20px;display:flex;align-items:center}
.submit{left:786px;top:4150px;width:112px;height:42px;background:var(--blue);border-radius:4px;font-size:13px;font-weight:500;display:flex;align-items:center;justify-content:center}
.foot-rule{left:110px;top:4255px;width:978px;height:1px;background:#3a3a3a}
.copyright{left:0;top:4277px;width:1200px;text-align:center;font-size:12.5px;font-weight:500}
</style>
</head>
<body>

<header>
  <div class="abs brand"><span class="brand-square"></span>Bracken Learning Films</div>
  <nav class="abs nav">
    <span>Home</span><span>About</span><span>Prices</span><span>Testimonials</span>
    <span>Videos<svg width="10" height="6" viewBox="0 0 10 6"><path d="M0 0h10L5 6z" fill="#1d1d1f"/></svg></span>
    <span>Contact Us</span>
  </nav>
  <div class="abs search"><svg width="16" height="16" viewBox="0 0 16 16"><circle cx="7" cy="7" r="5" fill="none" stroke="#fff" stroke-width="2"/><path d="M11 11l4 4" stroke="#fff" stroke-width="2" stroke-linecap="round"/></svg></div>
</header>

<section class="abs hero" role="img" aria-label="Classroom of pupils raising their hands while a teacher stands at the front"></section>
<div class="abs hero-text">
  <div class="hero-brand"><i></i>Bracken Learning Films</div>
  <h1>Educate a child</h1>
  <p>YOU EDUCATE A FAMILY</p>
  <p>WE MAKE AWESOME EDUCATIONAL VIDEOS</p>
</div>

<h2 class="abs heading" style="left:600px;top:713px"><span class="sq"></span><span><b>A</b>bout <b>U</b>s</span></h2>
<div class="abs about-copy">
  <p>Hi, I'm Owen Pardoe, Videographer, Content Creator, Filmmaker. Founder of Bracken Learning Films and dad of two. Thanks for stopping by.</p>
  <p>I've been producing all kinds of videos for over 25 years (from weddings and other live events to corporate and educational promotions – it's truly the best job in the world). At the age of eight, I was bitten by the videomaking bug and went on to study it at diploma and, later, degree level. And it's clearly still a big part of my life today.</p>
</div>
<div class="abs about-frame"></div>
<div class="abs about-photo" role="img" aria-label="Smiling schoolgirl raising her hand in class"></div>

<section>
  <div class="abs prices-band"></div>
  <h2 class="abs heading" style="left:600px;top:1362px"><span class="sq"></span><span><b>P</b>rices</span></h2>

  <div class="abs price-card" style="left:198px">
    <div class="price-head"><span>Promotional Videos</span><span>prices</span></div>
    <div class="price-from">START AT £1,200</div>
    <ul class="price-list"><li>A full day of filming</li><li>Drone filming</li><li>Production meeting on-site</li></ul>
    <div class="price-btn">VIEW DETAILS</div>
  </div>
  <div class="abs price-card" style="left:471px">
    <div class="price-head"><span>Live Performance Filming</span><span>prices</span></div>
    <div class="price-from">START AT £450</div>
    <ul class="price-list"><li>60minute performance – prices start at £450</li><li>Additional time charged at £100 per hour</li></ul>
    <div class="price-btn">VIEW DETAILS</div>
  </div>
  <div class="abs price-card" style="left:742px">
    <div class="price-head"><span>Residential Videos</span><span>prices</span></div>
    <div class="price-from" style="margin-top:14px">START AT £500</div>
    <ul class="price-list" style="margin-top:0"><li>1/2 Day Filming – from £500</li><li>1 Days Filming – from £800</li><li>2 Days Filming – from £1,400</li></ul>
    <div class="price-btn">VIEW DETAILS</div>
  </div>
  <div class="abs dots" style="left:541px;top:1843px"><i></i><i class="on"></i><i></i></div>
</section>

<section>
  <h2 class="abs heading" style="left:600px;top:2005px"><span class="sq"></span><span><b>P</b>romotional <b>V</b>ideos</span></h2>
  <article class="abs video-card" style="left:110px">
    <div class="thumb" role="img" aria-label="School entrance sign video still" style="background:linear-gradient(135deg,#2a4fb0,#5d7fd1 50%,#8a7d6b)"><span class="play"><svg width="12" height="14"><path d="M0 0l12 7-12 7z" fill="#000"/></svg></span></div>
    <h3>Alderbrook Primary School</h3><p>Prospectus Video</p>
  </article>
  <article class="abs video-card" style="left:441px">
    <div class="thumb" role="img" aria-label="College workshop with a caravan video still" style="background:linear-gradient(135deg,#9aa0a8,#d8d8d4 50%,#5d6670)"><span class="play"><svg width="12" height="14"><path d="M0 0l12 7-12 7z" fill="#000"/></svg></span></div>
    <h3>Wearmouth College</h3><p>Promotional Video</p>
  </article>
  <article class="abs video-card" style="left:771px">
    <div class="thumb" role="img" aria-label="College building exterior testimonial still" style="background:linear-gradient(180deg,#7f9cc7,#c9cfd8 55%,#4d4f7a)"><span class="play"><svg width="12" height="14"><path d="M0 0l12 7-12 7z" fill="#000"/></svg></span></div>
    <h3>Wearmouth College</h3><p>Testimonial Video</p>
  </article>
  <div class="abs dots" style="left:541px;top:2483px"><i></i><i class="on"></i><i></i></div>
</section>

<section>
  <h2 class="abs heading" style="left:600px;top:2587px"><span class="sq"></span><span><b>S</b>ubject <b>V</b>ideos</span></h2>
  <div class="abs tab tab-outline">Multi Video Packages</div>
  <div class="abs tab tab-solid">School Success</div>
  <p class="abs subject-intro">Clara Haldane, Head Teacher at Harbourview Primary School in Seaham gives her reasons for booking<br>Bracken Learning Films and the success they had with the videos.</p>
  <div class="abs tiles">
    <div class="tile"><div class="tile-icon" role="img" aria-label="Promotion icon"></div><h4>Promotion</h4><span class="go"><svg width="10" height="12"><path d="M2 1l6 5-6 5" fill="none" stroke="#1ab2e8" stroke-width="2"/></svg></span></div>
    <div class="tile"><div class="tile-icon" role="img" aria-label="Curriculum achievement icon"></div><h4>Curriculum<br>Achievement</h4><span class="go"><svg width="10" height="12"><path d="M2 1l6 5-6 5" fill="none" stroke="#1ab2e8" stroke-width="2"/></svg></span></div>
    <div class="tile"><div class="tile-icon" role="img" aria-label="Website improvement icon"></div><h4>Website Improvement</h4><span class="go"><svg width="10" height="12"><path d="M2 1l6 5-6 5" fill="none" stroke="#1ab2e8" stroke-width="2"/></svg></span></div>
    <div class="tile"><div class="tile-icon" role="img" aria-label="Feedback icon"></div><h4>Feedback</h4><span class="go"><svg width="10" height="12"><path d="M2 1l6 5-6 5" fill="none" stroke="#1ab2e8" stroke-width="2"/></svg></span></div>
  </div>
</section>

<section>
  <h2 class="abs heading heading-left"><span class="sq"></span><span><b>T</b>estimonials</span></h2>
  <div class="abs avatar" role="img" aria-label="Reviewer portrait" style="left:821px;background:linear-gradient(160deg,#8aa,#456)"></div>
  <div class="abs avatar" role="img" aria-label="Reviewer portrait" style="left:914px;background:linear-gradient(160deg,#3aa8e0,#1f6fb0);border-color:var(--blue)"></div>
  <div class="abs avatar" role="img" aria-label="Reviewer portrait" style="left:1007px;background:linear-gradient(160deg,#ccc,#5b6b4a)"></div>

  <div class="abs testi-box"></div>
  <div class="abs testi-photo" role="img" aria-label="Smiling man in denim shirt giving a thumbs up"></div>
  <p class="abs quote">I just wanted to say a huge thank you for our fabulous Christmas film. It is relaxed and orgasnic and totally captures the spirit or the school. I love the fact it is all about the children. I can't wait to share it with the parent. Thanks again and we will definitely keep you in mind for future events and recommend you to other schools.</p>
  <div class="abs testi-name">RUTH CALLOWAY,</div>
  <div class="abs testi-role">HEAD TEACHER, HOLLINS PRIMARY SCHOOL, JARROW</div>
  <div class="abs stars">
    <svg width="120" height="20" viewBox="0 0 120 20"><g fill="#f5b400"><path id="st" d="M10 1l2.6 6 6.4.5-4.9 4.2 1.5 6.3L10 14.6 4.4 18l1.5-6.3L1 7.5l6.4-.5z"/><use href="#st" x="24"/><use href="#st" x="48"/><use href="#st" x="72"/><use href="#st" x="96"/></g></svg>
  </div>
  <div class="abs arrow-btn" style="left:973px"><svg width="10" height="12"><path d="M8 1L2 6l6 5" fill="none" stroke="#fff" stroke-width="2"/></svg></div>
  <div class="abs arrow-btn" style="left:1016px"><svg width="10" height="12"><path d="M2 1l6 5-6 5" fill="none" stroke="#fff" stroke-width="2"/></svg></div>
</section>

<footer>
  <div class="abs footer"></div>
  <div class="abs foot-title" style="left:110px;top:3885px">Quick Links</div>
  <ul class="abs foot-links" style="left:110px;top:3933px;color:#fff">
    <li>Home</li><li>About</li><li>Prices</li><li>Testimonials</li><li>Contact Us</li><li>Promotional Videos</li><li>Subject Videos</li>
  </ul>
  <div class="abs foot-title" style="left:354px;top:3885px">Contact Us</div>
  <div class="abs contact-row" style="left:356px;top:3954px;color:#fff">
    <span class="contact-icon"><svg width="20" height="20" viewBox="0 0 24 24"><path d="M6.6 10.8a15 15 0 006.6 6.6l2.2-2.2a1 1 0 011-.25 11.4 11.4 0 003.6.57 1 1 0 011 1V20a1 1 0 01-1 1A17 17 0 013 4a1 1 0 011-1h3.5a1 1 0 011 1c0 1.25.2 2.45.57 3.6a1 1 0 01-.25 1z" fill="#fff"/></svg></span>07700 900 318
  </div>
  <div class="abs contact-row" style="left:356px;top:4024px;color:#fff">
    <span class="contact-icon"><svg width="20" height="16" viewBox="0 0 20 16"><rect x="1" y="1" width="18" height="14" rx="2" fill="none" stroke="#fff" stroke-width="2"/><path d="M2 2l8 7 8-7" fill="none" stroke="#fff" stroke-width="2"/></svg></span>info@brackenlearningfilms.co.uk
  </div>
  <div class="abs contact-row" style="left:356px;top:4093px;color:#fff;align-items:flex-start;line-height:39px">
    <span class="contact-icon"><svg width="16" height="20" viewBox="0 0 16 20"><path d="M8 1a7 7 0 017 7c0 5-7 11-7 11S1 13 1 8a7 7 0 017-7z" fill="none" stroke="#fff" stroke-width="2"/><circle cx="8" cy="8" r="2.5" fill="#fff"/></svg></span>
    <span style="margin-top:-2px">Unit 4, Fellside Trade Park,<br>Consett, Durham. DH8 5XQ.</span>
  </div>
  <div class="abs foot-title" style="left:786px;top:3885px">Reach Us</div>
  <div class="abs field" style="top:3947px;color:#fff">FULL NAME</div>
  <div class="abs field" style="top:4014px;color:#fff">EMAIL ADDRESS</div>
  <div class="abs field" style="top:4081px;color:#fff">TYPE YOUR MESSAGE</div>
  <div class="abs submit" style="color:#000">SUBMIT</div>
  <div class="abs foot-rule"></div>
  <div class="abs copyright" style="color:#fff">© BRACKEN LEARNING FILMS LIMITED 2023. ALL RIGHTS RESERVED.</div>
</footer>

</body>
</html>
```